Corporate Design für Apotheke
Zielgruppe
Gesundheitswesen, Apotheke Zielgruppe kranke Menschen aber auch 'shopper'.
Aufgabenstellung
Das alte Logo ist leider viel zu filigran. Bei verschiedenen Druck kommt es oft nicht raus. Früher war das Logo eckig, es wurde vor Jahren mal als rund modernisiert.
Bin aber offen für alles.
Apotheke sollte grundsätzlich mit den Werten Seriosität, Vertrauen , und in unserem Fall auch Exklusivität, Premium- Segment verbunden werden. Im Anhang unser altes Logo. Ich bin zum ersten mal hier und freue mich auf kreative Vorschläge

```html
<!DOCTYPE html>
<html lang="de">
<head>
<meta charset="utf-8">
<title>Lindenhain Apotheke – Geschäftsausstattung</title>
<link href="https://fonts.googleapis.com/css2?family=Jost:wght@400;500;700&family=Caveat:wght@400;500&display=swap" rel="stylesheet">
<style>
:root{
  --bg:#e2e2e2;
  --paper:#ffffff;
  --green-dark:#1f7a44;
  --green-card:#2e8351;
  --green-text:#2f9a45;
  --ink:#3a3a3a;
  --watermark:#e4f0e6;
}
*{margin:0;padding:0;box-sizing:border-box}
html,body{width:1200px;height:822px;overflow:hidden;background:var(--bg);font-family:"Jost",sans-serif;color:var(--ink)}
.canvas{position:relative;width:1200px;height:822px}

/* Letterhead */
.letterhead{position:absolute;left:40px;top:20px;width:553px;height:782px;background:var(--paper);overflow:hidden}
.fold-mark{position:absolute;left:5px;width:8px;height:1px;background:var(--green-text)}
.top-mark{position:absolute;left:389px;top:5px;width:1px;height:7px;background:var(--green-text)}
.claim{position:absolute;left:52px;top:64px;font-family:"Caveat",cursive;font-size:20px;color:var(--green-text)}

/* Name plate: plain circle beside the name, one weight, one colour */
.nameplate{display:flex;align-items:center;gap:8px}
.nameplate-dot{flex:none;width:22px;height:22px;border:2px solid var(--green-dark);border-radius:50%}
.nameplate-name{font-weight:500;font-size:15px;color:var(--green-dark);white-space:nowrap}
.letterhead .nameplate{position:absolute;left:354px;top:76px}

.sender-line{position:absolute;left:57px;top:120px;font-size:7.5px;color:var(--green-text)}
.recipient{position:absolute;left:65px;top:145px;font-size:8px;line-height:11px;font-style:normal}
.contact{position:absolute;left:354px;top:155px;font-size:7.5px;line-height:11px;color:var(--green-text)}
.contact dl{margin-top:8px;display:grid;grid-template-columns:24px auto}
.contact dt{font-weight:700;color:var(--green-dark)}
.letter-body{position:absolute;left:65px;top:275px;width:440px;font-size:7.8px;line-height:11.2px}
.subject{font-weight:700;font-size:8.2px;margin-bottom:22px}
.letter-body p{margin-bottom:11px}
.sign-off{margin-top:20px}
.watermark{position:absolute;left:417px;top:605px;width:160px;height:160px;border:9px solid var(--watermark);border-radius:50%}
.footer{position:absolute;left:0;bottom:0;width:100%;height:48px;background:var(--green-dark);color:#e6f3ea;font-size:7.4px;line-height:11px;padding:12px 0 0 52px}

/* Business cards */
.card{position:absolute;left:640px;width:340px;height:210px;box-shadow:0 2px 6px rgba(0,0,0,.12)}
.card-front{top:110px;background:var(--green-card);display:flex;align-items:center;justify-content:center}
.card-front .nameplate-dot{width:30px;height:30px;border-color:#fff}
.card-front .nameplate-name{color:#fff;font-size:20px}
.card-back{top:350px;background:var(--paper);padding:24px 24px 0 24px}
.person{font-weight:700;font-size:13.5px;letter-spacing:1px;color:var(--green-dark);width:222px;padding-bottom:5px;border-bottom:1px solid var(--green-text)}
.role{font-size:9px;color:var(--green-text);margin-top:7px}
.card-back .nameplate-dot{position:absolute;right:24px;top:22px;width:40px;height:40px}
.card-address{margin:22px 0 0 84px;font-size:8.5px;line-height:12px;color:var(--green-text)}
.card-address dl{margin-top:8px;display:grid;grid-template-columns:30px auto}
.card-address dt{font-weight:700;color:var(--green-dark)}
</style>
</head>
<body>
<main class="canvas">

  <article class="letterhead">
    <span class="top-mark"></span>
    <span class="fold-mark" style="top:276px"></span>
    <span class="fold-mark" style="top:391px"></span>
    <span class="fold-mark" style="top:554px"></span>

    <div class="claim">… Wir sind für Sie da!</div>

    <div class="nameplate">
      <span class="nameplate-dot"></span>
      <span class="nameplate-name">Lindenhain Apotheke</span>
    </div>

    <div class="sender-line">Lindenhain Apotheke | Lindenweg 4 | 70412 Auenbrunn</div>

    <address class="recipient">
      Clara Hofstetter<br>Ahornallee 12<br>01987 Feldmark
    </address>

    <div class="contact">
      Lindenweg 4 | 70412 Auenbrunn
      <dl>
        <dt>Fon:</dt><dd>012 345 78 90</dd>
        <dt>Web:</dt><dd>lindenhain-apotheke.de</dd>
        <dt>Mail:</dt><dd>kontakt@lindenhain-apotheke.de</dd>
      </dl>
    </div>

    <section class="letter-body">
      <div class="subject">Rechnungslegung November 2019</div>
      <p>Sehr geehrte Frau Hofstetter,</p>
      <p>Is evelibusant adist, simpori tatias volorem reicabore, omnitas explaut erum re officipsam aut acipic te volut fugit, apic minum fugiandant verum vellaut quibusapelit omnistrumet alitat dolecea verfere mporem restio. At facietus, con nos invel et ant, conesto de imolum, te int.</p>
      <p>Ibuscita soluptius quid quo to qui ullaut desti cumet laut et adit esequis cipit, odis vitia ditias ariorpo rionsedi dolori voluptatus nectiis dolupta speles quatemolupta vent illabor ibusdan ditaepe rissum essum rest que duciduntures est ra vendi rem que nulles int quatquodis et modignis dolorem volori ullut et ad est rem quisincid quatatur restemolupta su labo. Ipsunt ut quiae et quiderupta sit ius.</p>
      <p>Tust et voloris non pro occus, sequiditio eum cullaci dolut restrum apelit, nonsecabo. Neque restrum hil eum ipiet debis doluptur remquam que si bero ipsunt, conectur sapit quibus sit qui ut volo beat.</p>
      <p>Cerum earcidem facepero vit, tem ent voloruntem es magnimillaut mi, to eatiunt emoloratium ut eaquis quodi am quuntibuscit minissi dolupta doloreh enietur aut quam nulliquibus explitiorem re prenda placcae essequam hilique cu etur as ut earum rerio. Ur sum ne volor autemque volori doloratus.</p>
      <p class="sign-off">Mit freundlichen Grüßen</p>
      <p>Ihr Team der Lindenhain Apotheke</p>
    </section>

    <div class="watermark" aria-hidden="true"></div>

    <footer class="footer">
      Lindenhain Apotheke | Inhaber Apotheker Jonas Kerber | USt-IdNr. DE 308 552 917 | Handelsregisternr. HRB 703381<br>
      Mo – Fr 8.00 – 19.00 Uhr, Sa 10.00 – 14.00 Uhr | Bank XXXXXX | BIC XXXXXXXXXXX | IBAN DE19 5500 1200 0467 3301 88
    </footer>
  </article>

  <section class="card card-front">
    <div class="nameplate">
      <span class="nameplate-dot"></span>
      <span class="nameplate-name">Lindenhain Apotheke</span>
    </div>
  </section>

  <section class="card card-back">
    <div class="person">JONAS KERBER</div>
    <div class="role">Fachapotheker für Onkologie</div>
    <span class="nameplate-dot"></span>
    <div class="card-address">
      Lindenhain Apotheke<br>Lindenweg 4 | 70412 Auenbrunn
      <dl>
        <dt>Fon:</dt><dd>012 345 78 90</dd>
        <dt>Web:</dt><dd>lindenhain-apotheke.de</dd>
        <dt>Mail:</dt><dd>kontakt@lindenhain-apotheke.de</dd>
      </dl>
    </div>
  </section>

</main>
</body>
</html>
```